professional business card design

Business card design. Photos have been uploaded and i am open to the designer choosing which photos to use. Would like the card to be mostyly in a grey scale design with black, whites, silver & grey colours. I have added copy of our flyer as would like on the back side of card our services to be listed. Do not use any bright colurs such as blue red green or yellow. i need to be able to edit the phone number and naem in the final card design submitted.

Target Market(s)

Clients

Industry/Entity Type

earhmovibng and transport

Contact Information for Business Card

Director Name, address, email, phone number and services

Colors

Designer to choose only greyscale colors for use in the design.

Requirements
Should not have
• no yellow, red, blue or green

```html
<!DOCTYPE html>
<html lang="en">
<head>
<meta charset="utf-8">
<title>KVR Pty Ltd – Business Card</title>
<link href="https://fonts.googleapis.com/css2?family=Lato:wght@400;700;900&display=swap" rel="stylesheet">
<style>
  :root{
    --bg:#2b2b2d;
    --card:#0b0b0c;
    --card-mid:#1c1c1e;
    --metal:#3a3a3d;
    --silver:#d9d9db;
    --silver-dim:#a8a8ab;
    --grey:#5d5d60;
    --white:#ffffff;
  }
  *{box-sizing:border-box;margin:0;padding:0}
  html,body{width:1200px;height:962px;overflow:hidden}
  body{background:var(--bg);font-family:'Lato',sans-serif;position:relative}

  .card{position:absolute;border-radius:16px;overflow:hidden;
    background:radial-gradient(ellipse at 60% 30%,var(--metal) 0%,var(--card-mid) 45%,var(--card) 80%);
    box-shadow:0 12px 30px rgba(0,0,0,.55)}

  /* front */
  .card-front{left:93px;top:304px;width:620px;height:354px}
  .truck-photo{position:absolute;left:0;top:118px;width:560px;height:150px;
    background:linear-gradient(90deg,#4a4a4c 0%,#2c2c2e 40%,#1a1a1b 75%,rgba(20,20,20,0) 100%);
    border-radius:4px}
  .brand-front{position:absolute;left:238px;top:40px;text-align:center;color:var(--silver)}
  .brand-front .brand-name{display:block;font-weight:900;font-size:92px;line-height:1;letter-spacing:2px}
  .brand-front .brand-suffix{display:block;font-weight:900;font-size:20px;color:var(--silver-dim);margin-top:2px}

  .identity{position:absolute;left:26px;top:270px;width:238px;text-align:right}
  .identity .person{font-weight:900;font-size:27px;color:var(--silver-dim);letter-spacing:.5px}
  .identity .role{font-size:17px;color:var(--silver);margin-top:2px}
  .divider{position:absolute;left:282px;top:270px;width:2px;height:72px;background:var(--grey)}

  .contact{position:absolute;left:300px;top:266px;list-style:none;color:var(--silver)}
  .contact li{display:flex;align-items:flex-start;gap:10px;font-size:15px;line-height:1.25;margin-bottom:3px}
  .contact svg{flex:0 0 14px;margin-top:2px}
  .contact .phone{font-weight:900;font-size:19px;color:var(--white)}

  /* back */
  .card-back{left:753px;top:171px;width:354px;height:620px}
  .services-heading{position:absolute;left:26px;top:34px;width:240px;height:42px;background:var(--grey);
    color:var(--white);font-weight:900;font-size:22px;letter-spacing:1.5px;display:flex;align-items:center;padding-left:14px}
  .services-list{position:absolute;left:26px;top:94px;list-style:none;color:var(--white)}
  .services-list li{display:flex;gap:9px;font-size:16px;line-height:1.25;margin-bottom:6px}
  .services-list li::before{content:"›";flex:0 0 14px;height:14px;margin-top:2px;border-radius:50%;
    background:var(--white);color:var(--card);font-weight:900;font-size:13px;line-height:13px;text-align:center}
  .brand-back{position:absolute;left:0;right:0;bottom:40px;text-align:center;color:var(--silver)}
  .brand-back .brand-name{display:block;font-weight:900;font-size:80px;line-height:1;letter-spacing:2px}
  .brand-back .brand-suffix{display:block;font-weight:900;font-size:18px;color:var(--silver-dim)}
</style>
</head>
<body>

<section class="card card-front">
  <div class="truck-photo" role="img" aria-label="Photo of a road train truck hauling three tipper trailers"></div>
  <div class="brand-front">
    <span class="brand-name">KVR</span>
    <span class="brand-suffix">Pty Ltd</span>
  </div>
  <div class="identity">
    <p class="person">DANIEL HART</p>
    <p class="role">Director &amp; Founder</p>
  </div>
  <div class="divider"></div>
  <ul class="contact">
    <li>
      <svg width="14" height="18" viewBox="0 0 14 18"><path d="M7 1a5.5 5.5 0 0 0-5.5 5.5C1.5 11 7 17 7 17s5.5-6 5.5-10.5A5.5 5.5 0 0 0 7 1z" fill="none" stroke="#a8a8ab" stroke-width="1.5"/><circle cx="7" cy="6.5" r="2" fill="#a8a8ab"/></svg>
      <span>Your Address, City<br>State, Zip 1235</span>
    </li>
    <li>
      <svg width="14" height="16" viewBox="0 0 14 16"><path d="M3 1l3 3-1.6 2a9 9 0 0 0 4.6 4.6L11 9l3 3-2 2.5C6 14 .5 8.5 .5 3z" fill="#a8a8ab"/></svg>
      <span class="phone">(123) 456-7890</span>
    </li>
    <li>
      <svg width="14" height="12" viewBox="0 0 14 12"><rect x=".75" y=".75" width="12.5" height="10.5" fill="none" stroke="#a8a8ab" stroke-width="1.5"/><path d="M1 1l6 5 6-5" fill="none" stroke="#a8a8ab" stroke-width="1.5"/></svg>
      <span>info@yourwebsite.com</span>
    </li>
  </ul>
</section>

<section class="card card-back">
  <h2 class="services-heading">OUR SERVICES</h2>
  <ul class="services-list">
    <li>Over Size Loads / Hot Shot Loads</li>
    <li>Heavy Vehicle Recovery Services</li>
    <li>Poatable Water Deliveries</li>
    <li>Road Building / Maintenance</li>
    <li>Earthworks</li>
    <li>Sand &amp; Metal Supply &amp; Cartage</li>
    <li>Road Train Tippers</li>
    <li>Road Train Tankers</li>
    <li>Road Train Flat Tops</li>
    <li>Drop Dect Trailers</li>
    <li>Mine Site Accredited Equipment<br>and Operators</li>
  </ul>
  <div class="brand-back">
    <span class="brand-name">KVR</span>
    <span class="brand-suffix">Pty Ltd</span>
  </div>
</section>

</body>
</html>
```